Boutique Store Selling Antiques and Unique Finds

I need a Web Page designed for my Store Called "Willow Lane". I would like a very classic, muted design that looks European when pulled up. I will be selling Antiques from all over the world and Unique finds that have reproduced. I will also be selling high-end purses and jewelry with unique, reasonable products for the every-day buyer as well.

Target Market(s)

25-70 year old men and women;)

Coding

Coded - Design and coding required

Number of Pages Required

1 page

Colors

Designer to choose only greyscale colors for use in the design.

Requirements
Must have
• I want it

```html
<!DOCTYPE html>
<html lang="en">
<head>
<meta charset="utf-8">
<title>Willow Lane — Antiques and Unique Finds</title>
<link href="https://fonts.googleapis.com/css2?family=Cinzel:wght@400;600&family=Jost:wght@400;500;600&family=Arimo:wght@400;700&display=swap" rel="stylesheet">
<style>
:root{
  --ink:#1c1c1c;
  --black:#050505;
  --white:#ffffff;
  --paper:#f4f2ee;
  --mist:#efefef;
  --line:#8a8a8a;
  --soft-line:#bdbdbd;
  --muted:#555555;
  --pine:#263b37;
  --footer-text:#d9d9d9;
}
*{margin:0;padding:0;box-sizing:border-box}
html,body{width:1200px;height:3627px;overflow:hidden;background:var(--white);color:var(--ink);font-family:"Jost",sans-serif}
.page{position:relative;width:1200px;height:3627px}
.abs{position:absolute}
.center-text{text-align:center}

/* header */
.util{top:18px;font-size:11px;letter-spacing:.3px;text-transform:uppercase}
.nav a{position:absolute;top:72px;font-size:13px;letter-spacing:.4px;text-transform:uppercase;color:var(--ink);text-decoration:none}
.nav .active::after{content:"";position:absolute;left:-5px;right:-5px;top:37px;height:2px;background:var(--ink)}
.brand{top:58px;left:0;width:1200px;text-align:center;font-family:"Cinzel",serif;font-size:26px;letter-spacing:4px;color:var(--ink)}

/* hero */
.hero{top:115px;left:0;width:1200px;height:607px;background:linear-gradient(120deg,#6b5443 0%,#3d2c22 35%,#8a6d55 60%,#b8a389 85%,#d4c6b2 100%)}
.hero-frame{top:272px;left:103px;width:415px;height:270px;border:1px solid rgba(255,255,255,.55)}
.hero-box{top:282px;left:113px;width:397px;height:250px;background:#212121;color:var(--white)}
.hero-kicker{top:347px;left:113px;width:397px;font-size:17px;letter-spacing:2px}
.hero-title{top:368px;left:113px;width:397px;font-family:"Cinzel",serif;font-size:27px;line-height:36px}
.btn-ghost{top:456px;left:228px;width:168px;height:38px;border:1px solid var(--white);color:var(--white);font-size:12px;font-weight:600;letter-spacing:1.8px;line-height:36px}
.dot{width:7px;height:7px;border-radius:50%;background:rgba(255,255,255,.55)}
.dot.on{background:var(--white)}

/* section titles */
.section-title{left:0;width:1200px;font-size:27px;letter-spacing:3px;text-transform:uppercase;font-weight:400}
.section-title b{font-weight:600}
.rule{left:584px;width:32px;height:2px;background:var(--ink)}

/* product categories */
.cat{width:275px;height:259px;border:1px solid var(--line);background:var(--white)}
.cat .photo{position:absolute;left:7px;top:7px;right:7px;bottom:7px}
.cat .label{position:absolute;left:13px;right:13px;bottom:13px;height:44px;background:var(--paper);font-family:"Cinzel",serif;font-size:16px;letter-spacing:2px;line-height:44px;text-align:center}

/* about */
.about{top:1162px;left:0;width:1200px;height:557px;background:linear-gradient(90deg,#c9a36b 0%,#6b3a22 20%,#d9c299 40%,#7a4326 60%,#e2c79a 80%,#b98a52 100%)}
.about-card{top:1284px;left:655px;width:447px;height:316px;background:var(--paper)}
.about-card .inner{position:absolute;inset:11px;border:1px solid var(--muted)}
.about-kicker{top:1357px;left:655px;width:447px;font-size:14px;letter-spacing:1.5px;text-transform:uppercase}
.about-title{top:1376px;left:655px;width:447px;font-size:30px;letter-spacing:3px;text-transform:uppercase}
.about-title b{font-weight:600}
.about-text{top:1434px;left:690px;width:377px;font-family:"Arimo",sans-serif;font-size:12px;line-height:21px;color:#333}
.btn-solid{background:var(--pine);color:var(--white);font-size:11px;font-weight:600;letter-spacing:1px;text-transform:uppercase}

/* shop */
.item{width:326px;height:298px;border:1px solid var(--line);background:var(--white)}
.item .photo{position:absolute;left:0;top:0;right:0;height:220px}
.item .name{position:absolute;top:238px;width:100%;text-align:center;font-size:15px;letter-spacing:1px}
.item .price{position:absolute;top:262px;width:100%;text-align:center;font-family:"Arimo",sans-serif;font-size:14px;font-weight:700}
.dot-dark{width:7px;height:7px;border-radius:50%;background:var(--soft-line)}
.dot-dark.on{background:var(--pine)}

/* popular */
.popular{top:2271px;left:0;width:1200px;height:637px;background:var(--mist)}
.pop{width:497px;height:412px;border:1px solid var(--line);background:var(--white)}
.pop .photo{position:absolute;left:0;top:0;right:0;height:311px}
.pop .dash{position:absolute;top:336px;left:238px;width:20px;height:1px;background:var(--ink)}
.pop .name{position:absolute;top:342px;width:100%;text-align:center;font-size:17px;letter-spacing:1px;text-transform:uppercase}
.pop .price{position:absolute;top:370px;width:100%;text-align:center;font-family:"Arimo",sans-serif;font-size:14px;font-weight:700}

/* newsletter */
.news-title{left:0;width:1200px;font-size:26px;letter-spacing:3.5px;text-transform:uppercase}
.field{top:3098px;width:327px;height:47px;border:1px solid var(--line);font-size:12px;line-height:45px;padding-left:19px;color:#444}

/* footer */
.footer{top:3262px;left:0;width:1200px;height:365px;background:var(--black);color:var(--footer-text)}
.col-head{top:3334px;font-size:13px;text-transform:uppercase;color:var(--white)}
.col-links{top:3362px;font-size:10px;line-height:25.5px;list-style:none}
.col-div{top:3330px;width:1px;height:144px;background:#3a3a3a}
.foot-line{top:3541px;left:0;width:1200px;height:1px;background:#3a3a3a}
.foot-small{top:3577px;font-size:10px}
.foot-brand{top:3566px;left:0;width:1200px;text-align:center;font-family:"Cinzel",serif;font-size:22px;letter-spacing:3.5px;color:var(--white)}
</style>
</head>
<body>
<div class="page">

  <!-- header -->
  <div class="abs util" style="left:99px">My Account</div>
  <div class="abs util" style="left:1033px;top:24px">Basket (0)</div>
  <div class="abs brand">Willow Lane</div>
  <nav class="nav">
    <a class="active" style="left:96px">Home</a>
    <a style="left:183px">Shop Online</a>
    <a style="left:321px">Products</a>
    <a style="left:801px">Discover</a>
    <a style="left:914px">Blogs</a>
    <a style="left:1005px">Contact Us</a>
  </nav>

  <!-- hero -->
  <div class="abs hero" role="img" aria-label="Photo of a tufted antique sofa in a wood-panelled library room"></div>
  <div class="abs hero-frame"></div>
  <div class="abs hero-box"></div>
  <div class="abs hero-kicker center-text" style="color:#fff">SHOP NOW</div>
  <div class="abs hero-title center-text" style="color:#fff">ANTIQUES FROM<br>ALL OVER THE WORLD</div>
  <div class="abs btn-ghost center-text">VIEW PRODUCTS</div>
  <div class="abs dot on" style="left:579px;top:697px"></div>
  <div class="abs dot" style="left:597px;top:697px"></div>
  <div class="abs dot" style="left:615px;top:697px"></div>

  <!-- our products -->
  <h2 class="abs section-title center-text" style="top:766px">Our <b>Products</b></h2>
  <div class="abs rule" style="top:806px"></div>

  <div class="abs cat" style="left:45px;top:848px">
    <div class="photo" role="img" aria-label="Gilded antique dresser with lamps and a mantel clock" style="background:linear-gradient(160deg,#1a1a1a,#c9a24f 55%,#e8d9a8)"></div>
    <div class="label">ANTIQUES</div>
  </div>
  <div class="abs cat" style="left:328px;top:848px">
    <div class="photo" role="img" aria-label="Brass gramophone horn among shop curios" style="background:linear-gradient(160deg,#3a4552,#c9b03a 50%,#5a4a3a)"></div>
    <div class="label">SHOWPIECE</div>
  </div>
  <div class="abs cat" style="left:608px;top:848px">
    <div class="photo" role="img" aria-label="Brass vase and bell on a wooden table" style="background:linear-gradient(160deg,#3f6a2e,#8a5a36 45%,#6b4630)"></div>
    <div class="label">PURSES</div>
  </div>
  <div class="abs cat" style="left:888px;top:848px">
    <div class="photo" role="img" aria-label="Ornate gilt mantel clock" style="background:linear-gradient(160deg,#5a4030,#b08a4a 50%,#3a2a20)"></div>
    <div class="label">CLOCK</div>
  </div>

  <!-- about -->
  <div class="abs about" role="img" aria-label="Carved mahogany chaise sofa beneath gilt-framed paintings"></div>
  <div class="abs about-card"><div class="inner"></div></div>
  <div class="abs about-kicker center-text">About Us</div>
  <div class="abs about-title center-text"><b>Willow</b> Lane</div>
  <div class="abs rule" style="top:1419px;left:863px;width:30px"></div>
  <p class="abs about-text center-text">Lorem Ipsum is simply dummy text of the printing and typesetting industry. Lorem Ipsum has been the industry's standard dummy text ever since the 1500s, when an unknown printer.</p>
  <div class="abs btn-solid center-text" style="top:1515px;left:818px;width:131px;height:31px;line-height:31px">Learn More</div>

  <!-- shop online -->
  <h2 class="abs section-title center-text" style="top:1774px">Shop <b>Online</b></h2>
  <div class="abs rule" style="top:1819px"></div>

  <div class="abs item" style="left:94px;top:1853px">
    <div class="photo" role="img" aria-label="Carved antique upholstered sofa" style="background:linear-gradient(160deg,#2e2418,#8a5a30 50%,#b99a6a)"></div>
    <div class="name">PRODUCT ANTIQUE CHAIR</div>
    <div class="price">$1,350.00</div>
  </div>
  <div class="abs item" style="left:439px;top:1853px">
    <div class="photo" role="img" aria-label="Antique pistol, compass and gold coins on wood" style="background:linear-gradient(160deg,#4a4030,#b89a50 50%,#6a5a40)"></div>
    <div class="name">PRODUCT ANTIQUE CHAIR</div>
    <div class="price">$1,350.00</div>
  </div>
  <div class="abs item" style="left:786px;top:1853px">
    <div class="photo" role="img" aria-label="Painted brass figurines on a shop shelf" style="background:linear-gradient(160deg,#6a5a3a,#c9a03a 45%,#2a6a6a 70%,#8a2a2a)"></div>
    <div class="name">PRODUCT ANTIQUE CHAIR</div>
    <div class="price">$1,350.00</div>
  </div>
  <div class="abs dot-dark on" style="left:580px;top:2206px"></div>
  <div class="abs dot-dark" style="left:599px;top:2206px"></div>
  <div class="abs dot-dark" style="left:617px;top:2206px"></div>

  <!-- popular -->
  <div class="abs popular"></div>
  <h2 class="abs section-title center-text" style="top:2329px"><b>Popular</b> Items</h2>
  <div class="abs rule" style="top:2380px"></div>

  <div class="abs pop" style="left:110px;top:2412px">
    <div class="photo" role="img" aria-label="Gold and diamond necklace draped on driftwood" style="background:linear-gradient(150deg,#1a120c,#6a3e20 50%,#2a1a10)"></div>
    <div class="dash"></div>
    <div class="name">Jewelery Items</div>
    <div class="price">$1,150.00</div>
  </div>
  <div class="abs pop" style="left:627px;top:2412px">
    <div class="photo" role="img" aria-label="Designer leather handbag on a glass shelf" style="background:linear-gradient(150deg,#e8e2d8,#b9a070 45%,#2a2a2a 65%,#d8d2c6)"></div>
    <div class="dash"></div>
    <div class="name">High End Purses</div>
    <div class="price">$750.00</div>
  </div>

  <!-- newsletter -->
  <div class="abs news-title center-text" style="top:2987px;font-weight:600">Sign up to our newsletter</div>
  <div class="abs news-title center-text" style="top:3020px">To stay up to date</div>
  <div class="abs field" style="left:175px">Your Name</div>
  <div class="abs field" style="left:514px">Your Email address</div>
  <div class="abs btn-solid center-text" style="top:3097px;left:850px;width:176px;height:48px;line-height:48px;font-size:14px;letter-spacing:2px">Subscribe</div>

  <!-- footer -->
  <footer class="abs footer"></footer>
  <div class="abs col-head" style="left:158px">About Us</div>
  <ul class="abs col-links" style="left:158px"><li>A Family Business</li><li>Philosophy and Ethos</li><li>Charity and Community</li><li>Press</li><li>Careers</li></ul>
  <div class="abs col-div" style="left:358px"></div>
  <div class="abs col-head" style="left:428px">Special Events</div>
  <ul class="abs col-links" style="left:428px"><li>Workshops</li><li>Private Events Richmond</li><li>Private Events Covent Garden</li><li>Supper Clubs</li></ul>
  <div class="abs col-div" style="left:656px"></div>
  <div class="abs col-head" style="left:736px">Resources</div>
  <ul class="abs col-links" style="left:736px"><li>Terms and Conditions</li><li>Privacy Policy</li><li>Contact</li></ul>
  <div class="abs col-div" style="left:917px"></div>
  <div class="abs col-head" style="left:986px">Social</div>
  <ul class="abs col-links" style="left:986px"><li>Snapwall</li><li>Friendbook</li><li>Pinboard</li><li>Chirper</li></ul>

  <div class="abs foot-line"></div>
  <div class="abs foot-small" style="left:179px">2021 © Willow Lane &nbsp;|&nbsp; All Right Reserved</div>
  <div class="abs foot-brand">Willow Lane</div>
  <div class="abs foot-small" style="left:887px">Cookies</div>
  <div class="abs foot-small" style="left:942px">Sitemap</div>
  <div class="abs foot-small" style="left:998px">Terms of Use</div>

</div>
</body>
</html>
```